KVOR Individual and Corporate Development Business Card Design

KVOR needs a business card design that is aligned with it's values and targetted markets. Coherent Lattice of Adaptive Reasoning Method's self diagnosis model and tools, which can be used for personal improvement and team/business performance enhancement, is based on the learnings of over 20 years of medical practitioning. KVOR supercharges personal effectiveness and awareness to also increase team and business performance.

The targetted markets are high performance individuals and teams who aspire seek to enhance their capabilities and achieve their absolute best potential.

Look and feel for the business card design we are looking for is high technology, premium, fresh, new and medical.

Target Market(s)

Industry/Entity Type

Business Consultant

Contact Information for Business Card

Logo, Full Name, Title, Phone number, Email, company name, Address,

Font styles to use
Sans Serif

Requirements
Must have
• Tag line: Amplifying Potential for Truly Ambitious Achievers
• Please use same colours as the logo.

```html
<!DOCTYPE html>
<html lang="en">
<head>
<meta charset="utf-8">
<title>KVOR Business Card</title>
<link href="https://fonts.googleapis.com/css2?family=Open+Sans:wght@400;600;700&display=swap" rel="stylesheet">
<style>
  :root {
    --stage: #ecebea;
    --card-light: #f4f2f1;
    --card-light-edge: #e4e1df;
    --card-dark: #252325;
    --brand-teal: #1ba6bb;
    --text-white: #ffffff;
    --text-soft: #e8e8e8;
    --rule: #8a8a8a;
  }
  * { margin: 0; padding: 0; box-sizing: border-box; }
  html, body {
    width: 1200px; height: 900px; overflow: hidden;
    background: var(--stage);
    font-family: "Open Sans", Arial, sans-serif;
  }
  .canvas { position: relative; width: 1200px; height: 900px; }

  .card {
    position: absolute;
    box-shadow: 0 6px 18px rgba(0,0,0,0.18);
    overflow: hidden;
  }
  .card--front { left: 237px; top: 62px; width: 556px; height: 342px; }
  .card--back  { left: 457px; top: 519px; width: 560px; height: 341px; }

  .card__brand-panel {
    position: absolute; left: 0; top: 0; width: 100%;
    background: linear-gradient(180deg, var(--card-light) 0%, var(--card-light-edge) 100%);
    display: flex; align-items: center; justify-content: center;
  }
  .card--front .card__brand-panel { height: 183px; }
  .card--back .card__brand-panel { height: 186px; }

  .card__info-panel {
    position: absolute; left: 0; bottom: 0; width: 100%;
    background: var(--card-dark);
  }
  .card--front .card__info-panel { height: 159px; }
  .card--back .card__info-panel { height: 155px; }

  .brand-name {
    display: flex; align-items: center; gap: 14px;
    color: var(--brand-teal);
    font-weight: 700; font-size: 58px; letter-spacing: 4px; line-height: 1;
  }
  .brand-name__mark {
    width: 16px; height: 16px; background: var(--brand-teal);
  }
  .brand-name--through { transform: scaleX(-1); opacity: 0.9; }

  .person {
    position: absolute; left: 61px; top: 41px; color: var(--text-white);
  }
  .person__name { font-weight: 700; font-size: 18px; letter-spacing: 0.2px; }
  .person__title { font-size: 15px; color: var(--text-soft); margin-top: 2px; }

  .contact-divider {
    position: absolute; left: 300px; top: 42px; width: 1px; height: 48px;
    background: var(--rule);
  }
  .contact-list {
    position: absolute; left: 319px; top: 40px; list-style: none;
    color: var(--text-white); font-size: 14.5px; line-height: 17px;
  }
  .contact-list li { display: flex; align-items: center; gap: 9px; }
  .contact-list svg { width: 10px; height: 10px; fill: var(--brand-teal); flex: none; }
  .contact-list .icon-mail { fill: var(--brand-teal); stroke: var(--card-dark); stroke-width: 1; }

  .address {
    position: absolute; left: 0; right: 0; top: 112px; text-align: center;
    color: var(--text-white); font-size: 14.5px;
  }

  .tagline-block {
    position: absolute; left: 0; right: 0; top: 56px; text-align: center;
    font-weight: 700;
  }
  .tagline-block__company { color: var(--brand-teal); font-size: 15px; }
  .tagline-block__line { color: var(--text-white); font-size: 15.5px; margin-top: 2px; }
</style>
</head>
<body>
<main class="canvas">

  <section class="card card--front" aria-label="Business card front">
    <div class="card__brand-panel">
      <div class="brand-name"><span class="brand-name__mark"></span>KVOR</div>
    </div>
    <div class="card__info-panel">
      <div class="person">
        <div class="person__name">MARCUS ELLERY</div>
        <div class="person__title">Managing Director</div>
      </div>
      <div class="contact-divider"></div>
      <ul class="contact-list">
        <li><svg viewBox="0 0 10 10"><rect x="2.5" y="0" width="5" height="10" rx="1"/></svg>888 555 777</li>
        <li><svg class="icon-mail" viewBox="0 0 10 10"><rect x="0" y="2" width="10" height="6"/><path d="M0.5 2.5L5 5.5L9.5 2.5" fill="none"/></svg>info@kvor.com</li>
        <li><svg viewBox="0 0 10 10"><circle cx="5" cy="5" r="5"/></svg>www.kvor.com</li>
      </ul>
      <div class="address">Address line one here, Address line two here.</div>
    </div>
  </section>

  <section class="card card--back" aria-label="Business card back">
    <div class="card__brand-panel">
      <div class="brand-name brand-name--through"><span class="brand-name__mark"></span>KVOR</div>
    </div>
    <div class="card__info-panel">
      <div class="tagline-block">
        <div class="tagline-block__company">KVOR</div>
        <div class="tagline-block__line">AMPLIFYING POTENTIAL FOR TRULY AMBITIOUS ACHIEVERS</div>
      </div>
    </div>
  </section>

</main>
</body>
</html>
```